Adult Literacy Program - flyer to attract volunteers and students

We want a flyer that is engaging, colorful, modern and will appeal to our primary audience of adults aged 40-60. We are trying to attract both prospective volunteers (typically age 50+, mostly women) and students (typically aged 40+).
The flyer should feature diverse people working together in pairs of two, reading or talking, with a workbook or some reading material in front of them.

Our organization trains tutors to work one-on-one with adults who are learning how to read. Most of our adult students are non-native speakers of English. Many are of Haitian or Hispanic origin, so we would like some people who represent that demographic.

The Flyer should represent reading, learning, literacy, knowledge, growth,
and opportunities.
Our students are learning to read so they can advance their job opportunities.

Target Market(s)

Adults aged 40-60, primarily women, retired, volunteers

Industry/Entity Type

Education

Font styles to use
Serif
Sans Serif

Colors

Designer to choose colors to be used in the design.

Requirements
Must have
• - UPDATE: Should be designed as a TRI-FOLD brochure on 8.5 x 11 inch paper that will be folded into thirds.
• - Images of diverse people, women and men, who look Hispanic, Haitian and other nationalities as well as Caucasian.
• - Our logo on the front cover
Nice to have
• The sample flyer is very boring and dry! We are open to different ways of presenting the text.

```html
<!DOCTYPE html>
<html lang="en">
<head>
<meta charset="utf-8">
<title>Reading Bridge Partners – Tri-fold Brochure</title>
<link href="https://fonts.googleapis.com/css2?family=Open+Sans:wght@400;600;700;800&display=swap" rel="stylesheet">
<style>
:root{
  --navy:#0c1f5e;
  --blue:#1d9ad6;
  --paper:#f4f4f6;
  --paper-shade:#dcdde1;
  --ink:#14224f;
  --white:#ffffff;
  --page:#e9e9eb;
}
*{margin:0;padding:0;box-sizing:border-box}
html,body{width:847px;height:1200px;overflow:hidden;background:var(--page);font-family:"Open Sans",Arial,sans-serif;color:var(--ink)}
.canvas{position:relative;width:847px;height:1200px}
.spread{position:absolute;left:46px;width:757px;height:535px;display:flex;box-shadow:0 4px 14px rgba(0,0,0,.25)}
.spread--outside{top:45px}
.spread--inside{top:620px}
.spread::after{content:"";position:absolute;left:0;right:0;bottom:0;height:4px;background:linear-gradient(90deg,var(--navy),var(--blue))}
.panel{position:relative;width:252px;height:100%;overflow:hidden}
.panel--navy{background:var(--navy)}
.panel--light{background:linear-gradient(90deg,var(--paper-shade),var(--paper) 30%,var(--paper) 70%,var(--paper-shade))}
.photo{position:absolute;left:0;width:100%}
.heading{font-weight:700;font-size:20px;letter-spacing:.5px;text-transform:uppercase}
.rule{width:30px;height:2px;margin:6px 0 10px}
.ticks{list-style:none;font-size:11px;line-height:1.35}
.ticks li{position:relative;padding-left:14px;margin-bottom:5px}
.ticks li::before{content:"✓";position:absolute;left:0;top:0}
/* tutors panel */
.tutors{position:absolute;left:30px;top:30px;right:8px;color:var(--white)}
.tutors .rule{background:var(--white)}
.tagline{margin-top:18px;line-height:1.05;text-transform:uppercase}
.tagline .big{display:block;font-weight:800;font-size:22px}
.tagline .small{display:block;font-weight:400;font-size:17px}
/* brand lockup */
.brand-lockup{display:flex;flex-direction:column;align-items:center;gap:6px}
.brand-mark{display:block;width:12px;height:12px;border-radius:50%;background:var(--blue)}
.brand{color:var(--blue);font-weight:700;font-size:12px;line-height:1.25;text-transform:uppercase;letter-spacing:1px}
/* contact panel */
.contact{position:absolute;left:0;right:0;top:110px;text-align:center}
.cta{margin-top:22px;font-weight:800;font-size:21px;line-height:1.15;text-transform:uppercase;color:var(--navy)}
.cta span{display:block;font-size:18px;font-weight:700}
.cta-rule{width:50px;height:2px;background:var(--navy);margin:8px auto 12px}
.contact p{font-size:11px;line-height:1.4}
.contact .strong{font-weight:700;font-size:12.5px;color:var(--navy)}
.contact .detail{display:flex;align-items:flex-start;justify-content:center;gap:5px;font-weight:600;font-size:11px;margin-top:10px;color:var(--ink)}
.contact .detail svg{flex:none;margin-top:2px}
.partner{margin-top:22px;display:flex;align-items:center;justify-content:center;gap:6px;font-weight:700;font-size:11px;color:var(--navy)}
.partner i{display:block;width:11px;height:11px;background:var(--navy)}
/* volunteer panel */
.vol-head{position:absolute;top:0;left:0;right:0;height:58px;background:linear-gradient(90deg,var(--navy),#1565a8);color:var(--white);font-weight:800;font-size:30px;text-align:center;line-height:58px;letter-spacing:.5px}
.enrich{position:absolute;top:309px;left:0;right:0;height:85px;background:var(--navy);color:var(--white);text-align:center;padding-top:10px}
.enrich h2{font-weight:800;font-size:24px;line-height:1}
.enrich .rule{background:var(--white);width:50px;margin:5px auto 4px}
.enrich p{font-size:12px;line-height:1.3;text-transform:uppercase}
.enrich p b{font-weight:800;font-size:13px}
.cover-brand{position:absolute;top:430px;left:0;right:0;text-align:center}
.cover-brand .brand{font-size:13px}
/* students panel */
.students{position:absolute;left:32px;top:30px;right:10px}
.students .heading{color:var(--navy)}
.students .rule{background:var(--navy)}
.students .lead{font-weight:700;font-size:11px;margin-bottom:4px}
.students .ticks li{margin-bottom:2px}
.students .ticks.bold{margin-top:9px;font-weight:600}
.slogan{margin-top:10px;line-height:1.1;text-transform:uppercase}
.slogan span{display:block;font-size:17px}
.slogan b{display:block;font-weight:800;font-size:22px;color:var(--navy)}
/* info panels */
.info{position:absolute;left:32px;right:26px;top:358px;color:var(--white)}
.info .rule{background:var(--white)}
.info p{font-size:8.6px;line-height:1.45}
</style>
</head>
<body>
<main class="canvas">

  <section class="spread spread--outside">
    <div class="panel panel--navy">
      <div class="tutors">
        <h2 class="heading">Tutors</h2>
        <div class="rule"></div>
        <ul class="ticks">
          <li>No special skills or degrees<br>needed — just a degree of caring!</li>
          <li>Training offered throughout the year</li>
          <li>Tutors meet students weekly<br>at a library</li>
          <li>Instructional materials provided</li>
          <li>Ongoing support available</li>
        </ul>
        <p class="tagline"><span class="big">Teach an adult</span><span class="small">to read and</span><span class="big">you'll change</span><span class="big">a life forever</span></p>
      </div>
      <div class="photo" style="top:325px;height:210px;background:linear-gradient(135deg,#8a6d52,#c9b59c 55%,#6f7d8e)" role="img" aria-label="Smiling woman tutor at a library table with adults studying in the background"></div>
    </div>

    <div class="panel panel--light">
      <div class="contact">
        <div class="brand-lockup">
          <span class="brand-mark"></span>
          <div class="brand">Reading Bridge<br>Partners</div>
        </div>
        <h2 class="cta">Don't waste<span>a moment!</span></h2>
        <div class="cta-rule"></div>
        <p class="strong">Contact us today</p>
        <p>to learn more.</p>
        <p class="strong" style="font-size:11px">Volunteer Desk</p>
        <div class="detail"><svg width="10" height="10" viewBox="0 0 10 10"><circle cx="5" cy="5" r="4.3" fill="none" stroke="#14224f" stroke-width="1"/><path d="M3.4 2.8l1 1-.6.7c.4.8.9 1.3 1.7 1.7l.7-.6 1 1-.7.8C4.6 7.1 2.9 5.4 2.7 3.5z" fill="#14224f"/></svg>555-201-4780</div>
        <div class="detail"><svg width="8" height="11" viewBox="0 0 8 11"><path d="M4 10.5S.5 6.3.5 4a3.5 3.5 0 017 0c0 2.3-3.5 6.5-3.5 6.5z" fill="none" stroke="#14224f"/><circle cx="4" cy="4" r="1.2" fill="#14224f"/></svg><span>Lakeview, Palmhurst<br>&amp; South Harbor</span></div>
        <div class="detail"><svg width="10" height="10" viewBox="0 0 10 10"><circle cx="5" cy="5" r="4.3" fill="none" stroke="#14224f" stroke-width="1"/><path d="M3.4 2.8l1 1-.6.7c.4.8.9 1.3 1.7 1.7l.7-.6 1 1-.7.8C4.6 7.1 2.9 5.4 2.7 3.5z" fill="#14224f"/></svg>555-201-4791</div>
        <div class="detail"><svg width="11" height="8" viewBox="0 0 11 8"><rect x=".5" y=".5" width="10" height="7" fill="none" stroke="#14224f"/><path d="M.5.5l5 4 5-4" fill="none" stroke="#14224f"/></svg>literacy@coastalreads.org</div>
        <div class="partner"><i></i>Coastal County Library</div>
      </div>
    </div>

    <div class="panel panel--light">
      <div class="vol-head">VOLUNTEER</div>
      <div class="photo" style="top:58px;height:251px;background:linear-gradient(135deg,#5f7ea6,#b9a58e 50%,#3d4f6e)" role="img" aria-label="Older man with glasses helping an adult learner read in a library"></div>
      <div class="enrich">
        <h2>ENRICH A LIFE!</h2>
        <div class="rule"></div>
        <p>Help an adult learn to read<br><b>write or speak English</b></p>
      </div>
      <div class="cover-brand">
        <div class="brand-lockup">
          <span class="brand-mark"></span>
          <div class="brand">Reading Bridge<br>Partners</div>
        </div>
      </div>
    </div>
  </section>

  <section class="spread spread--inside">
    <div class="panel panel--light" style="background:linear-gradient(90deg,#f7f7f8,#e6e7ea)">
      <div class="students">
        <h2 class="heading">Students</h2>
        <div class="rule"></div>
        <p class="lead">Students are adults in need of</p>
        <ul class="ticks">
          <li>basic literacy skills</li>
          <li>pre-diploma skills</li>
          <li>conversational English</li>
        </ul>
        <ul class="ticks bold">
          <li>Tutoring is free of charge</li>
          <li>Tutoring is one-on-one</li>
          <li>Flexible scheduling during<br>library hours</li>
          <li>Lessons focus on student goals</li>
        </ul>
        <p class="slogan"><span>If you can read,</span><b>you can tutor!</b></p>
      </div>
      <div class="photo" style="top:290px;height:245px;background:linear-gradient(135deg,#d9c7a6,#e8d9c3 45%,#b8533f)" role="img" aria-label="Two women reading a book together at a library table"></div>
    </div>

    <div class="panel panel--navy">
      <div class="photo" style="top:0;height:335px;background:linear-gradient(135deg,#3e4a36,#a88e70 50%,#e2d6c4)" role="img" aria-label="Smiling woman holding a book talking with a tutor"></div>
      <div class="info">
        <h2 class="heading">About us</h2>
        <div class="rule"></div>
        <p>Lorem ipsum dolor sit amet, consectetur adipiscing elit, sed do eiusmod tempor incididunt ut labore et dolore magna aliqua. Ut enim ad minim veniam, quis nostrud exercitation ullamco laboris nisi ut aliquip ex ea commodo consequat. Duis aute irure dolor in reprehenderit in voluptate velit esse cillum dolore eu fugiat nulla pariatur.</p>
      </div>
    </div>

    <div class="panel panel--navy">
      <div class="photo" style="top:0;height:172px;background:linear-gradient(135deg,#c9ccd2,#8d9aac 50%,#c3a84a)" role="img" aria-label="Diverse adults studying together at a library table"></div>
      <div class="photo" style="top:172px;height:163px;background:linear-gradient(135deg,#b59b7a,#4f6b55 50%,#8b8fa4)" role="img" aria-label="Group of smiling adult learners and tutors seated at a table"></div>
      <div class="info">
        <h2 class="heading">Why choose us</h2>
        <div class="rule"></div>
        <p>Lorem ipsum dolor sit amet, consectetur adipiscing elit, sed do eiusmod tempor incididunt ut labore et dolore magna aliqua. Ut enim ad minim veniam, quis nostrud exercitation ullamco laboris nisi ut aliquip ex ea commodo consequat. Duis aute irure dolor in reprehenderit in voluptate velit esse cillum dolore eu fugiat nulla pariatur.</p>
      </div>
    </div>
  </section>

</main>
</body>
</html>
```